Belvascotravel.com web design project + logo design

Hi,

We are a Russian online tour operator - sunkettle.com

We are looking to tranmsfer our domain to belvascotravel.com. The website and logo need to be belvascoesque - we are not looking to change our functionality, but we need to make the website much more attracitve to clients, much more wild looking but at the same time remaining a professional travel company.

The main concept of the website should be innovative travel (as belvasco was an innovator). Alternatively, you could go down the artist route and go down the draw / design your own tour road.

On our website the customer is able to combine travel services (hotels, flights, Visa services, and soon chauffeur, car rental etc...) put it into their basket (the basket definitely has to look better than it is at the moment) and pay for it in one go by card.

We are also stressin our customer support with web chat, call centre etc... (call centre number at the top of the page)

We aim to provide an easy user experience, but we need to make it have some more style, so I will be waiting for what you guys can come up with.
Let me know if you have any questions - skype is: mrdolbarin

Industry/Entity Type

It Company

Requirements
Must have
• It is quite a simple task - to take the existing website sunkettle.com and belvascosize it to create belvascotravel.com, the functionality of the website will remain the same and there are not many pages in the website. Homepage, Checkout step1, Checkout step 2 (you can view both of these if you select a service) and the generic pages for T&C''s, Privacy policy etc...

IMPORTANT UPDATE

We are also looking at how the search results will look in the designs, (please do a search on our website for hotel / flight)

```html
<!DOCTYPE html>
<html lang="en">
<head>
<meta charset="utf-8">
<title>Belvascotravel.com</title>
<link href="https://fonts.googleapis.com/css2?family=PT+Sans:ital,wght@0,400;0,700;1,400&family=PT+Serif:ital@0;1&display=swap" rel="stylesheet">
<style>
:root{
  --blue:#0a7fc7;
  --blue-dark:#0563a4;
  --blue-text:#1a6fb3;
  --bg:#eef1f3;
  --panel:#dde3e7;
  --green:#62b72d;
  --green-dark:#4a9a1d;
  --text:#444;
  --muted:#8a9298;
  --footer:#1c1c1c;
  --white:#fff;
}
*{box-sizing:border-box;margin:0;padding:0}
html,body{width:999px;height:1200px;overflow:hidden}
body{position:relative;background:var(--bg);font-family:"PT Sans",Arial,sans-serif;color:var(--text);font-size:11px}
.abs{position:absolute}
.top-line{left:0;top:0;width:999px;height:3px;background:var(--blue)}
.header{left:0;top:3px;width:999px;height:112px;background:#f2f3f4}
.brand{left:93px;top:42px;display:flex;align-items:center;gap:6px;font-size:20px;font-weight:700;color:var(--blue-dark)}
.brand .dot{width:16px;height:16px;border-radius:50%;background:var(--green)}
.call{right:94px;top:22px;text-align:right;color:#444;font-size:13px}
.call .num{display:block;color:var(--blue);font-size:14px;margin-top:2px}
.call svg{vertical-align:-2px;margin-right:4px}
.search{left:731px;top:79px;width:174px;height:22px;background:#fff;border:1px solid #e0e3e5;border-radius:3px;color:#c4c8cb;font-size:10px;padding:5px 7px}
.search svg{position:absolute;right:6px;top:3px}
.nav{left:0;top:115px;width:999px;height:31px;background:linear-gradient(#1b8fd6,#0a6fb6);display:flex;align-items:center}
.nav a{position:absolute;color:#fff;text-decoration:none;font-size:12px;transform:translateX(-50%)}
.nav a.home{left:87px;transform:none;background:#fff;color:var(--blue-dark);font-weight:700;padding:3px 12px;border-radius:2px}
.nav .sep{position:absolute;top:5px;width:1px;height:21px;background:rgba(255,255,255,.25)}
.hero{left:0;top:146px;width:999px;height:389px;background:linear-gradient(#5f9ee8 0%,#a8cdf0 50%,#3ea6cc 58%,#6cc3d6 75%,#d9d4c4 100%)}
.welcome{left:0;top:478px;width:450px;height:92px;background:linear-gradient(#fff,#eceef0);box-shadow:0 3px 6px rgba(0,0,0,.2)}
.welcome h1{position:absolute;left:97px;top:10px;font-weight:400;font-size:20px;color:var(--blue-text)}
.welcome p{position:absolute;left:100px;top:38px;width:340px;font-size:10.5px;line-height:13px;color:#666}
.avail{left:669px;top:275px;width:224px;height:253px;background:#f4f5f6;box-shadow:0 1px 4px rgba(0,0,0,.2)}
.avail-tab{left:663px;top:275px;width:204px;height:31px;background:var(--blue);color:#fff;font-size:15px;padding:6px 0 0 36px;box-shadow:0 3px 4px rgba(0,0,0,.25)}
.avail-tab svg{position:absolute;left:10px;top:8px}
.field{position:absolute;left:676px;width:205px;height:20px;background:#fff;border:1px solid #dcdfe2;color:var(--blue-dark);font-size:10.5px;padding:3px 8px}
.field::after{content:"";position:absolute;right:6px;top:8px;border:4px solid transparent;border-top-color:#999}
.lbl{font-size:10.5px;color:#333}
.sel{left:751px;top:426px;width:62px;height:18px;background:#fff;border:1px solid #d6dade;color:var(--blue-dark);font-size:9px;padding:2px 4px}
.check{display:inline-block;width:8px;height:8px;background:var(--blue);margin-right:6px;vertical-align:-1px}
.btn-green{left:691px;top:491px;width:169px;height:27px;border-radius:3px;background:linear-gradient(#7ccb3f,var(--green-dark));color:#fff;font-size:15px;text-align:center;line-height:27px;border:1px solid #4a9a1d}
.svc-title{left:93px;top:588px;font-size:16px;color:var(--blue-text)}
.stripes{left:196px;top:595px;width:405px;height:8px;background:repeating-linear-gradient(135deg,#d0d5d9 0 1px,transparent 1px 3px)}
.arrows{left:612px;top:593px;color:#999;font-size:9px}
.svc-sub{left:93px;top:622px;font-size:13px;color:#444}
.svc-desc{left:93px;top:640px;font-size:10px;color:#777}
.btn-gallery{left:93px;top:664px;width:170px;height:24px;background:var(--green);color:#fff;font-size:10.5px;padding:5px 11px}
.feat{position:absolute;top:704px;width:46px;height:46px;border-radius:50%;background:#dfe3e6;border:1px solid #c8cdd1;display:flex;align-items:center;justify-content:center}
.feat-lbl{position:absolute;top:760px;font-family:"PT Serif",Georgia,serif;font-size:10.5px;color:#555;text-align:center;line-height:20px}
.room{left:294px;top:622px;width:340px;height:171px;background:#fff;padding:3px;box-shadow:0 1px 3px rgba(0,0,0,.2)}
.room div{width:100%;height:100%;background:linear-gradient(120deg,#b8965e,#8a5a34 50%,#4a3a42)}
.price{left:527px;top:634px;width:113px;height:24px;background:var(--blue);color:#fff;font-size:14px;font-style:italic;padding:3px 11px}
.body-p{left:98px;top:813px;width:535px;font-size:10.5px;line-height:16px;color:var(--muted)}
.side{left:657px;top:585px;width:250px;height:233px;background:var(--panel)}
.side-card{left:672px;top:600px;width:220px;height:58px;background:#fff}
.side-mark{left:676px;top:604px;width:70px;height:51px;background:#eef1f3;display:flex;align-items:center;justify-content:center;font-size:8px;font-weight:700;color:var(--blue-dark)}
.side-name{left:750px;top:605px;font-size:15px;color:var(--blue-text)}
.side-p{left:672px;top:676px;width:222px;font-size:10.5px;line-height:15.5px;color:var(--muted)}
.more{left:673px;top:779px;font-family:"PT Serif",Georgia,serif;font-style:italic;font-size:11px;color:#333}
.rule{left:97px;top:887px;width:534px;height:1px;background:#d6dbde}
.gallery{left:91px;top:908px;width:816px;height:223px;background:var(--panel)}
.card{position:absolute;top:932px;width:176px}
.card .ph{height:105px;background:#fff;padding:4px}
.card .ph div{width:100%;height:100%}
.card h3{font-weight:400;font-size:12px;color:var(--blue-text);margin:10px 0 6px 2px}
.card p{font-size:10.5px;line-height:12.5px;color:#333;margin-left:2px}
.garrow{position:absolute;top:1026px;width:23px;height:24px;background:var(--blue);display:flex;align-items:center;justify-content:center}
.footer{left:0;top:1160px;width:999px;height:40px;background:var(--footer);color:#ccc;text-align:center;line-height:40px;font-size:11.5px}
</style>
</head>
<body>
<div class="abs top-line"></div>
<header class="abs header"></header>
<div class="abs brand"><span class="dot"></span>belvascotravel.com</div>
<div class="abs call"><svg width="12" height="12" viewBox="0 0 24 24"><path fill="#1a4f8a" d="M6.6 10.8a15 15 0 0 0 6.6 6.6l2.2-2.2c.3-.3.7-.4 1-.2 1.1.4 2.3.6 3.6.6.6 0 1 .4 1 1V20c0 .6-.4 1-1 1A17 17 0 0 1 3 4c0-.6.4-1 1-1h3.5c.6 0 1 .4 1 1 0 1.3.2 2.5.6 3.6.1.3 0 .7-.2 1z"/></svg>You call, we're there<span class="num">+7 (495) 555-01-28</span></div>
<div class="abs search">Search<svg width="15" height="15" viewBox="0 0 24 24"><circle cx="10" cy="10" r="6.5" fill="none" stroke="#1a95dc" stroke-width="2.6"/><path d="M15 15l6 6" stroke="#1a95dc" stroke-width="3"/></svg></div>

<nav class="abs nav">
  <a class="home" href="#">HOME</a>
  <span class="sep" style="left:178px"></span>
  <a href="#" style="left:266px">Destinations</a>
  <span class="sep" style="left:350px"></span>
  <a href="#" style="left:424px">Activities</a>
  <span class="sep" style="left:494px"></span>
  <a href="#" style="left:576px">Trip Styles</a>
  <span class="sep" style="left:648px"></span>
  <a href="#" style="left:736px">Responsible</a>
  <span class="sep" style="left:816px"></span>
  <a href="#" style="left:885px">Travel</a>
</nav>

<div class="abs hero" role="img" aria-label="Woman in a blue dress looking out over a tropical bay with islands and a long-tail boat"></div>

<section class="abs welcome">
  <h1>Welcome to Belvasco Travles</h1>
  <p>Lorem Ipsum is simply dummy text of the printing and typesetting industry. Lorem Ipsum has been the industry's standard dummy text ever since the 1500s, when an unknown printer took a galley of type and scrambled</p>
</section>

<div class="abs avail"></div>
<div class="abs avail-tab"><svg width="18" height="16" viewBox="0 0 20 18"><circle cx="8" cy="6" r="4" fill="none" stroke="#fff" stroke-width="1.6"/><path d="M1 17c0-4 3-6 7-6s7 2 7 6" fill="none" stroke="#fff" stroke-width="1.6"/><circle cx="15" cy="10" r="2.5" fill="none" stroke="#fff" stroke-width="1.4"/></svg>Check Availablity</div>
<div class="field" style="top:327px">Откуда</div>
<div class="field" style="top:350px">Куда</div>
<div class="field" style="top:375px">Туда</div>
<div class="field" style="top:398px">Обратно</div>
<div class="abs lbl" style="left:682px;top:428px">Пассажиры</div>
<div class="abs sel">select</div>
<div class="abs lbl" style="left:682px;top:452px">Класс</div>
<div class="abs lbl" style="left:718px;top:451px"><span class="check"></span>Обратно</div>
<div class="abs lbl" style="left:718px;top:466px"><span class="check"></span>В одну сторону</div>
<div class="abs btn-green">View Availablity</div>

<h2 class="abs svc-title" style="font-weight:400">Our Services</h2>
<div class="abs stripes"></div>
<div class="abs arrows">◀ ▶</div>
<div class="abs svc-sub">Hoteling Services</div>
<div class="abs svc-desc">Lorem Ipsum is simply dummy text</div>
<div class="abs btn-gallery">The bed Rooms show on Gallery</div>
<div class="feat" style="left:98px"><svg width="26" height="24" viewBox="0 0 26 24"><path d="M13 2L1 13h4v10h6v-7h4v7h6V13h4z" fill="#333"/></svg></div>
<div class="feat" style="left:154px"><svg width="28" height="18" viewBox="0 0 28 18"><rect x="2" y="6" width="24" height="7" rx="2" fill="none" stroke="#333" stroke-width="2"/><circle cx="7" cy="5" r="3" fill="#333"/><path d="M3 13v4M25 13v4" stroke="#333" stroke-width="2"/></svg></div>
<div class="feat" style="left:211px"><svg width="24" height="24" viewBox="0 0 24 24"><path d="M4 22V9a6 6 0 0 1 12 0" fill="none" stroke="#333" stroke-width="2.4"/><path d="M12 9h8l-2 4h-4z" fill="#333"/><path d="M14 16l1 1M17 16l1 2M20 15l1 2M15 20l1 1M19 20l1 1" stroke="#333" stroke-width="1.4"/></svg></div>
<div class="feat-lbl" style="left:98px;width:46px">4500 sq<br>ft</div>
<div class="feat-lbl" style="left:154px;width:46px">5 Beds</div>
<div class="feat-lbl" style="left:211px;width:46px">2 Baths</div>
<div class="abs room"><div role="img" aria-label="Hotel bedroom with a striped bedspread, lamps and a window"></div></div>
<div class="abs price">$ 325.500</div>
<p class="abs body-p">Aliquam erat volutpat. Duis blandit augue ac orci laoreet eget condimentum magna venenatis. Maecenas eget augue in nisl malesuada mollis. Vivamus eget bibendum dolor. Nulla vel varius mi. In hac habitasse platea dictumst. Duis</p>

<aside class="abs side"></aside>
<div class="abs side-card"></div>
<div class="abs side-mark">belvascotravel</div>
<div class="abs side-name">Belvasco Travel</div>
<p class="abs side-p">Duis ac nisi et libero suscipit lobortis ac at velit. Cum sociis natoque penatibus et magnis dis parturient montes, nascetur ridiculus mus. Suspendisse ac nibh id magna adipiscing venenatis ac eu eros. Morbi euismod auctor ipsum, eget mollis eros</p>
<div class="abs more">View more →</div>

<div class="abs rule"></div>

<section class="abs gallery"></section>
<div class="garrow" style="left:87px"><svg width="10" height="12" viewBox="0 0 10 12"><path d="M8 1L3 6l5 5" fill="none" stroke="#fff" stroke-width="2.4"/></svg></div>
<div class="card" style="left:119px"><div class="ph"><div role="img" aria-label="Smiling family on holiday" style="background:linear-gradient(135deg,#e0566b,#f0c07a 50%,#8cc6e8)"></div></div><h3>Lorem Lipsum</h3><p>Lorem Ipsum is simply dummy text of the printing and typesetting industry. Lorem</p></div>
<div class="card" style="left:312px"><div class="ph"><div role="img" aria-label="Green island and a long-tail boat on turquoise water" style="background:linear-gradient(#5aa0dc,#3f7a3a 40%,#37b7cf 60%,#a9e0e6)"></div></div><h3>Lorem Lipsum</h3><p>Lorem Ipsum is simply dummy text of the printing and typesetting industry. Lorem</p></div>
<div class="card" style="left:504px"><div class="ph"><div role="img" aria-label="Limestone cliffs and boats on a beach" style="background:linear-gradient(#6a8a7a,#8fb0b6 50%,#b8a27c)"></div></div><h3>Lorem Lipsum</h3><p>Lorem Ipsum is simply dummy text of the printing and typesetting industry. Lorem</p></div>
<div class="card" style="left:698px"><div class="ph"><div role="img" aria-label="Hiker looking over a blue sea from a hilltop" style="background:linear-gradient(#8fb6dc,#2f6fa6 55%,#4a4a3a)"></div></div><h3>Lorem Lipsum</h3><p>Lorem Ipsum is simply dummy text of the printing and typesetting industry. Lorem</p></div>
<div class="garrow" style="left:889px"><svg width="10" height="12" viewBox="0 0 10 12"><path d="M2 1l5 5-5 5" fill="none" stroke="#fff" stroke-width="2.4"/></svg></div>

<footer class="abs footer">Copyright © 2013 . All rights reserved •</footer>
</body>
</html>
```